Hot Consulting firm collateral upgrade

We need a stationary design for our Oakland based consulting company called Talvora. We provide consulting expertise in KLT compliance for Medical Device, Pharmaceutical, and Biotech companies. We will be using the stationary for all of our marketing collateral. We want the design to convey professionalism and quality. You can find our company color scheme from our website talvora-advisory.com. I have included a copy of our current stationary that needs an upgrade.
Target Market(s)
Medical Device, Pharma, and Biotech companies
Industry/Entity Type
It Company
Look and feel

```html
<!DOCTYPE html>
<html lang="en">
<head>
<meta charset="utf-8">
<title>Talvora Business Card</title>
<link href="https://fonts.googleapis.com/css2?family=Mulish:wght@400;700&display=swap" rel="stylesheet">
<style>
  :root {
    --backdrop: #1c1c1e;
    --paper: #f4f4f3;
    --paper-shade: #e6e6e4;
    --rule-grey: #c9c9c9;
    --brand-blue: #1f4f9e;
    --brand-blue-deep: #163f86;
    --ink-grey: #4b4b4d;
    --text-grey: #555558;
    --white: #ffffff;
  }
  html, body {
    margin: 0;
    padding: 0;
    width: 1200px;
    height: 1000px;
    overflow: hidden;
    background: var(--backdrop);
    font-family: "Mulish", "Century Gothic", sans-serif;
  }
  .canvas {
    position: relative;
    width: 1200px;
    height: 1000px;
  }
  .card {
    position: absolute;
    width: 576px;
    height: 322px;
    border-radius: 18px;
    overflow: hidden;
  }
  /* Front */
  .card-front {
    left: 203px;
    top: 150px;
    background: var(--brand-blue);
  }
  .front-top {
    position: absolute;
    left: 0; top: 0;
    width: 100%;
    height: 180px;
    background: linear-gradient(180deg, var(--paper) 0%, var(--paper-shade) 100%);
  }
  .front-rule {
    position: absolute;
    left: 0; top: 180px;
    width: 100%;
    height: 7px;
    background: var(--rule-grey);
  }
  .front-bottom {
    position: absolute;
    left: 0; top: 187px;
    width: 100%;
    height: 135px;
    background: linear-gradient(180deg, var(--brand-blue) 0%, var(--brand-blue-deep) 100%);
  }
  .address {
    position: absolute;
    left: 29px;
    top: 78px;
    font-size: 13px;
    line-height: 17.5px;
    color: var(--text-grey);
  }
  .wordmark {
    position: absolute;
    display: flex;
    align-items: center;
    gap: 10px;
    font-weight: 400;
    line-height: 1;
    letter-spacing: -1px;
  }
  .wordmark-front {
    right: 30px;
    top: 74px;
    font-size: 54px;
    color: var(--ink-grey);
  }
  .wordmark-dot {
    display: inline-block;
    width: 16px;
    height: 16px;
    border-radius: 50%;
    background: var(--brand-blue);
  }
  .contact-list {
    position: absolute;
    left: 30px;
    top: 232px;
    margin: 0;
    padding: 0;
    list-style: none;
    font-size: 14px;
    line-height: 18px;
    color: var(--white);
  }
  .contact-list li {
    display: flex;
    align-items: center;
    gap: 8px;
  }
  .contact-icon {
    width: 14px;
    height: 14px;
    flex: none;
  }
  .person {
    position: absolute;
    right: 29px;
    top: 229px;
    text-align: right;
    color: var(--white);
  }
  .person-name {
    margin: 0;
    font-size: 19px;
    font-weight: 700;
    letter-spacing: 0.3px;
  }
  .person-title {
    margin: 2px 0 0;
    font-size: 15px;
    font-weight: 400;
  }
  /* Back */
  .card-back {
    left: 421px;
    top: 549px;
    background: radial-gradient(ellipse at 60% 35%, #2458aa 0%, var(--brand-blue) 45%, var(--brand-blue-deep) 100%);
  }
  .wordmark-back {
    right: 44px;
    top: 148px;
    font-size: 40px;
    color: var(--white);
  }
  .wordmark-back .wordmark-dot {
    width: 12px;
    height: 12px;
    background: var(--white);
  }
</style>
</head>
<body>
<main class="canvas">
  <section class="card card-front" aria-label="Business card front">
    <div class="front-top"></div>
    <div class="front-rule"></div>
    <div class="front-bottom"></div>

    <p class="address" style="margin:0">Bay Area HQ<br>4120 Harbor Mill Road<br>Oakland, CA 94607</p>

    <div class="wordmark wordmark-front"><span>talvora</span><span class="wordmark-dot"></span></div>

    <ul class="contact-list">
      <li>
        <svg class="contact-icon" viewBox="0 0 14 14" aria-hidden="true"><rect width="14" height="14" rx="2" fill="#fff"/><path d="M4 3.2c.5-.3 1 0 1.3.6l.5 1.1c.2.4 0 .8-.3 1l-.4.3c.4.9 1.1 1.6 2 2l.3-.4c.2-.3.6-.5 1-.3l1.1.5c.6.3.9.8.6 1.3-.4.8-1.2 1.3-2 1.1C5.8 9.9 4.1 8.2 3.6 5.9c-.2-.9.2-2.1.4-2.7z" fill="#1f4f9e"/></svg>
        (510) 555-0142
      </li>
      <li>
        <svg class="contact-icon" viewBox="0 0 14 14" aria-hidden="true"><rect width="14" height="14" rx="2" fill="#fff"/><rect x="2.5" y="4" width="9" height="6" fill="none" stroke="#1f4f9e" stroke-width="1.2"/><path d="M2.5 4l4.5 3.5L11.5 4" fill="none" stroke="#1f4f9e" stroke-width="1.2"/></svg>
        info@talvora-advisory.com
      </li>
      <li>
        <svg class="contact-icon" viewBox="0 0 14 14" aria-hidden="true"><rect width="14" height="14" rx="2" fill="#fff"/><circle cx="7" cy="7" r="4.3" fill="none" stroke="#1f4f9e" stroke-width="1.1"/><ellipse cx="7" cy="7" rx="1.8" ry="4.3" fill="none" stroke="#1f4f9e" stroke-width="1"/><path d="M2.7 7h8.6" stroke="#1f4f9e" stroke-width="1"/></svg>
        www.talvora-advisory.com
      </li>
    </ul>

    <div class="person">
      <p class="person-name">JORDAN MERCER</p>
      <p class="person-title">Account Executive</p>
    </div>
  </section>

  <section class="card card-back" aria-label="Business card back">
    <div class="wordmark wordmark-back"><span>talvora</span><span class="wordmark-dot"></span></div>
  </section>
</main>
</body>
</html>
```